Business card (AI file uploaded)

We need a business card design that is minimalist using existing logo (attached). Source files must be editable so we can make the same design with other names.

Screenshots included of a design I was working on to give you an idea of the style I would like. Looking for similar modern styles

Thanks

```html
<!DOCTYPE html>
<html lang="en">
<head>
<meta charset="utf-8">
<title>Marlow Law Group – Business Card</title>
<link href="https://fonts.googleapis.com/css2?family=Open+Sans:wght@300;400;600;700&display=swap" rel="stylesheet">
<style>
  :root {
    --backdrop: #cfcfcf;
    --card-front: #0b0b0b;
    --card-back: #3a3a3a;
    --ink-white: #ffffff;
    --ink-name: #8e8e8e;
    --ink-title: #6f6f6f;
    --ink-muted: #9a9a9a;
    --tab-grey: #a3a3a3;
  }
  * { box-sizing: border-box; margin: 0; padding: 0; }
  html, body {
    width: 1200px;
    height: 894px;
    overflow: hidden;
    background: var(--backdrop);
    font-family: "Open Sans", Arial, sans-serif;
  }
  .canvas {
    position: relative;
    width: 1200px;
    height: 894px;
  }
  .card {
    position: absolute;
    left: 260px;
    width: 680px;
    height: 388px;
    overflow: hidden;
    box-shadow: 0 10px 26px rgba(0,0,0,0.22);
  }
  .card--front { top: 40px; background: var(--card-front); }
  .card--back  { top: 466px; background: var(--card-back); }

  /* brand lockup */
  .brand {
    position: absolute;
    display: flex;
    align-items: center;
    gap: 16px;
  }
  .brand__mark {
    width: 64px;
    height: 64px;
    border-radius: 50%;
    background: var(--ink-white);
    flex: none;
  }
  .brand__name {
    color: var(--ink-white);
    font-weight: 400;
    font-size: 30px;
    line-height: 1.05;
    letter-spacing: 2px;
    text-transform: uppercase;
  }
  .card--front .brand { left: 40px; top: 36px; }
  .card--back .brand {
    left: 50%;
    top: 96px;
    transform: translateX(-50%);
  }

  /* accent tabs */
  .tab { position: absolute; background: var(--tab-grey); }
  .card--front .tab { left: 0; top: 128px; width: 26px; height: 40px; }
  .card--back .tab  { right: 0; top: 262px; width: 18px; height: 54px; }

  /* holder */
  .holder { position: absolute; left: 44px; top: 132px; }
  .holder__name {
    color: var(--ink-name);
    font-weight: 700;
    font-size: 25px;
    letter-spacing: 1.5px;
    text-transform: uppercase;
    line-height: 1.1;
  }
  .holder__title {
    color: var(--ink-title);
    font-weight: 400;
    font-size: 12px;
    letter-spacing: 4.5px;
    text-transform: uppercase;
    margin-top: 2px;
  }

  /* contact list */
  .contacts {
    position: absolute;
    left: 420px;
    top: 250px;
    list-style: none;
  }
  .contacts__item {
    display: flex;
    align-items: flex-start;
    gap: 12px;
    color: var(--ink-white);
    font-size: 12.5px;
    font-weight: 600;
    line-height: 1.25;
    margin-bottom: 9px;
  }
  .contacts__icon {
    width: 15px;
    height: 15px;
    flex: none;
    margin-top: 1px;
  }

  /* social row */
  .social {
    position: absolute;
    left: 0;
    right: 0;
    top: 300px;
    display: flex;
    justify-content: center;
    gap: 92px;
    list-style: none;
  }
  .social__item {
    display: flex;
    align-items: center;
    gap: 10px;
    color: var(--ink-muted);
    font-size: 13px;
    font-weight: 400;
  }
  .social__badge {
    width: 18px;
    height: 18px;
    background: var(--ink-muted);
    border-radius: 2px;
  }
</style>
</head>
<body>
<main class="canvas">

  <section class="card card--front" aria-label="Business card front">
    <div class="brand">
      <span class="brand__mark"></span>
      <span class="brand__name">Marlow<br>Law Group</span>
    </div>

    <span class="tab"></span>

    <div class="holder">
      <p class="holder__name">Evan Calder</p>
      <p class="holder__title">General Manager</p>
    </div>

    <ul class="contacts">
      <li class="contacts__item">
        <svg class="contacts__icon" viewBox="0 0 16 16" aria-hidden="true">
          <path d="M8 1.5 1 7.5h2v7h3.8v-4.5h2.4v4.5H13v-7h2z" fill="#9a9a9a"/>
        </svg>
        <span>27 9th floor, Harbor<br>Street NKL</span>
      </li>
      <li class="contacts__item">
        <svg class="contacts__icon" viewBox="0 0 16 16" aria-hidden="true">
          <g fill="none" stroke="#9a9a9a" stroke-width="1.3">
            <circle cx="8" cy="8" r="6.3"/>
            <ellipse cx="8" cy="8" rx="2.8" ry="6.3"/>
            <path d="M1.7 8h12.6M2.8 4.8h10.4M2.8 11.2h10.4"/>
          </g>
        </svg>
        <span>www.yourwebsite.com</span>
      </li>
      <li class="contacts__item">
        <svg class="contacts__icon" viewBox="0 0 16 16" aria-hidden="true">
          <rect x="1" y="3.5" width="14" height="9.5" fill="#9a9a9a"/>
          <path d="M1 3.5 8 9l7-5.5" fill="none" stroke="#0b0b0b" stroke-width="1.2"/>
        </svg>
        <span>yourname@email.com</span>
      </li>
      <li class="contacts__item">
        <svg class="contacts__icon" viewBox="0 0 16 16" aria-hidden="true">
          <path d="M4 1.5 6.3 4.8 4.9 6.4c.8 1.8 2.2 3.3 4 4.2l1.6-1.4 3.3 2.3-1.2 2.6C7.4 14 2.1 8.6 1.6 3z" fill="#9a9a9a"/>
        </svg>
        <span>012 345 6789</span>
      </li>
    </ul>
  </section>

  <section class="card card--back" aria-label="Business card back">
    <div class="brand">
      <span class="brand__mark"></span>
      <span class="brand__name">Marlow<br>Law Group</span>
    </div>

    <ul class="social">
      <li class="social__item"><span class="social__badge"></span>yourname</li>
      <li class="social__item"><span class="social__badge"></span>@yourname</li>
      <li class="social__item"><span class="social__badge"></span>yourname</li>
    </ul>

    <span class="tab"></span>
  </section>

</main>
</body>
</html>
```